Diverse, up-scale salon needs eye-catching, unique business cards.

We are looking for a unique business card design for our stylist but that can also be multi functional and used for appointment reminder and referrals. I will need a design in a format that I can modify names and titles going forward. In the past we have had a dark background with the logo on one side, and stylist and contact information on the other but we are open to all ideas. I have included our mission statement as well as branded colors below. The statement doesn't need to go on the card, it's just a reference for target market. We need space for the stylists name, title, instagram handle and then the salons phone number, website and address. I am also open to adding a spot for a qr code linked to the stylist instagram or the salon booking link.

primary brand colors:
#333333 #233415 #36502a #93874a #000000
Mission statement:
Vessolin Hair Studio, a high-end salon located in the lively Downtown Farmington, Michigan, is committed to providing exceptional services in a welcoming and relaxed environment to meet the needs of our diverse clientele.
Our salon specializes in contemporary custom haircuts, coloring, extensions, and barbering and beard grooming services. Our team of skilled stylists is passionate and inventive in their hair styling techniques. At the heart of our salon are values centered on quality, innovation, creativity, and above all, comfort. These core values are evident in every appointment across our customizable array of services.
Our goal is to establish a benchmark for exceptional hair care for every human.
Website: www.vessolinhairstudio.example
instagram: @vessolinhairstudio
address: 41782 Pelham Crest Rd, Alder Falls OR
phone: 555-613-4087

Industry/Entity Type

Hair Salon

Contact Information for Business Card

Stylist name, title, phone, instagram, website, address, (optional qr code)

Requirements
Should not have
• Does not need mission statement on the card.

```html
<!DOCTYPE html>
<html lang="en">
<head>
<meta charset="utf-8">
<title>Vessolin Hair Studio – Business Card</title>
<link href="https://fonts.googleapis.com/css2?family=Arimo:wght@400;700&display=swap" rel="stylesheet">
<style>
  :root{
    --gold:#93874a;
    --charcoal:#333333;
    --grey-text:#707070;
    --grey-band:#85827b;
    --rule:#8a8a8a;
    --white:#ffffff;
    --backdrop:#1b1b1b;
  }
  *{margin:0;padding:0;box-sizing:border-box}
  html,body{width:1200px;height:1059px;overflow:hidden;background:var(--backdrop);font-family:"Arimo",Arial,sans-serif}
  .canvas{position:relative;width:1200px;height:1059px}
  .card{position:absolute;overflow:hidden}
  .card-front{left:258px;top:89px;width:689px;height:394px;background:var(--white)}
  .card-back{left:252px;top:540px;width:701px;height:401px;background:var(--charcoal)}

  .brand-mark{position:absolute;border:3px solid var(--gold);border-radius:50%;display:flex;align-items:center;justify-content:center;text-align:center;color:var(--gold);font-weight:700;line-height:1.15}
  .card-front .brand-mark{left:454px;top:41px;width:188px;height:188px;font-size:19px}
  .card-back .brand-mark{left:233px;top:57px;width:224px;height:224px;font-size:23px}

  .stylist-name{position:absolute;left:40px;top:214px;font-size:21px;font-weight:700;color:var(--gold);letter-spacing:.2px}
  .stylist-title{position:absolute;left:40px;top:237px;font-size:15px;color:var(--grey-text)}
  .divider{position:absolute;left:40px;top:262px;width:609px;height:1.5px;background:var(--rule)}

  .contact{position:absolute;left:40px;font-size:19px;color:var(--grey-text);display:flex;align-items:center;gap:7px}
  .contact-phone{top:288px}
  .contact-social{top:317px}
  .contact svg{width:15px;height:15px;flex:none}
  .address{position:absolute;right:40px;top:293px;text-align:right;font-size:18.5px;line-height:24px;color:var(--grey-text);font-style:normal}

  .band-grey{position:absolute;left:0;bottom:0;width:346px;height:15px;background:var(--grey-band);clip-path:polygon(0 0,100% 0,calc(100% - 12px) 100%,0 100%)}
  .band-gold{position:absolute;right:0;bottom:0;width:344px;height:31px;background:var(--gold);clip-path:polygon(27px 0,100% 0,100% 100%,0 100%)}
  .website{position:absolute;right:40px;bottom:5px;font-size:19px;color:var(--white)}

  .services-head{position:absolute;left:48px;top:319px;width:603px;height:26px}
  .services-head::before,.services-head::after{content:"";position:absolute;top:12px;width:215px;height:1.5px;background:#d8d8d8}
  .services-head::before{left:0}
  .services-head::after{right:0}
  .services-pill{position:absolute;left:220px;top:0;width:164px;height:26px;border-radius:13px;background:var(--gold);color:var(--charcoal);font-size:18px;font-weight:700;display:flex;align-items:center;justify-content:center}
  .services-list{position:absolute;left:48px;top:355px;width:606px;display:flex;justify-content:space-between;list-style:none;color:var(--white);font-size:17.5px;white-space:nowrap}
  .services-list li::before{content:"";display:inline-block;width:7px;height:7px;border-radius:50%;background:var(--white);margin-right:5px;vertical-align:middle;position:relative;top:-2px}
</style>
</head>
<body>
<main class="canvas">
  <section class="card card-front" aria-label="Card front">
    <div class="brand-mark">Vessolin<br>Hair Studio</div>
    <h1 class="stylist-name">MARCUS ELLERY</h1>
    <p class="stylist-title">Manager</p>
    <div class="divider"></div>
    <p class="contact contact-phone">
      <svg viewBox="0 0 24 24" aria-hidden="true"><path fill="var(--gold)" d="M6.6 10.8a15.1 15.1 0 0 0 6.6 6.6l2.2-2.2c.3-.3.7-.4 1-.2 1.1.4 2.3.6 3.6.6.6 0 1 .4 1 1V20c0 .6-.4 1-1 1A17 17 0 0 1 3 4c0-.6.4-1 1-1h3.5c.6 0 1 .4 1 1 0 1.3.2 2.5.6 3.6.1.3 0 .7-.2 1z"/></svg>
      555-613-4087
    </p>
    <p class="contact contact-social">
      <svg viewBox="0 0 24 24" aria-hidden="true"><rect x="3" y="3" width="18" height="18" rx="5" fill="none" stroke="var(--gold)" stroke-width="2.5"/></svg>
      @vessolinhairstudio
    </p>
    <address class="address">41782 Pelham Crest Rd<br>Alder Falls OR</address>
    <div class="band-grey"></div>
    <div class="band-gold"></div>
    <p class="website">www.vessolinhairstudio.example</p>
  </section>

  <section class="card card-back" aria-label="Card back">
    <div class="brand-mark">Vessolin<br>Hair Studio</div>
    <div class="services-head"><span class="services-pill">OUR SERVICES</span></div>
    <ul class="services-list">
      <li>Custom Haircuts</li>
      <li>Coloring</li>
      <li>Extensions</li>
      <li>And Barbering</li>
      <li>Beard Grooming</li>
    </ul>
  </section>
</main>
</body>
</html>
```